Logo & Visitenkarte für Schreinermonteur (Fenster und Türen)
Sehr gute Designerin, gute Ideen und sie hat alle Änderungswünsche sehr schnell und genau umgesetzt. Jederzeit gerne wieder!
Zielgruppe
Verkauf und Einbau von Fenster und Türen (Bauelemente). Meine Zielgruppen sind Menschen, die ein Haus bauen oder renovieren und Fenster und Türen benötigen. Ich mache die Berautung und baue anschliessend die Türen, Fenster und Jalousien auch mit meinem Team ein.
Aufgabenstellung
Ich bin selbständiger Schreiner im Südschwarzwald und derzeit auf den Einbau von Fenster und Türen spezialisiert. Ich möchte meine Initialien RM in meinem Logo enthalten haben, bin aber auch offen für andere Vorschläge. Derzeit bin ich unter 'RM Tischlermontagen' bekannt.
Gerne darf als Untertitel 'Fenster und Türen' verwendet werden. Da ich die Option haben möchte, dass ich das Logo/meine Initialien weiterverwende, aber meine Spezialisierung von 'Fenster und Türen' ändere, sollte dies zwar im Logo enthalten sein, aber nicht zu stark integriert sein.
Ich arbeite in einer ländlichen Gegend und das Logo sollte Zuverlässigkeit, Flexibilität und Individualität ausstrahlen und einen hohen Widererkennungswert haben, da es viele andere Schreiner hier gibt. Ich bin bekannt für meine exakte und qualitativ hochwertige Arbeit und bin auch ein Spezialist, wenn es um die Beratung meiner Kunden bei der Fenster und Türenauswahl geht.
Bei den Farben bin ich noch etwas unentschlossen. Derzeit habe ich grau-blau als Farben, bin aber offen für andere Vorschläge. Nur bitte kein rot/rosa. Falls Fragen sind, bitte einfach kurz schreiben.
Besten Dank vorab für die Vorschläge!

```html
<!DOCTYPE html>
<html lang="de">
<head>
<meta charset="utf-8">
<title>RM Wendt – Visitenkarten</title>
<link href="https://fonts.googleapis.com/css2?family=Roboto:wght@400;700&display=swap" rel="stylesheet">
<style>
  :root {
    --backdrop: #00121c;
    --navy: #0a0a6b;
    --paper: #ffffff;
    --ink: #1a1a1a;
    --rule: #555555;
  }
  * { box-sizing: border-box; margin: 0; padding: 0; }
  html, body { width: 1200px; height: 818px; overflow: hidden; }
  body {
    background: var(--backdrop);
    font-family: "Roboto", Arial, sans-serif;
    position: relative;
  }
  .card {
    position: absolute;
    width: 469px;
    height: 287px;
    background: var(--paper);
    overflow: hidden;
  }
  .card--front-a { left: 125px; top: 87px; }
  .card--back    { left: 607px; top: 87px; }
  .card--front-b { left: 123px; top: 443px; }
  .card--front-c { left: 605px; top: 443px; }

  .shape { position: absolute; left: 0; top: 0; width: 469px; height: 287px; }

  .wordmark {
    position: absolute;
    left: 0; width: 100%;
    text-align: center;
    color: var(--navy);
    font-weight: 700;
    font-size: 28px;
    letter-spacing: 0.2px;
  }
  .card--front-a .wordmark { top: 124px; }
  .card--front-b .wordmark { top: 122px; }
  .card--front-c .wordmark { top: 122px; }

  .services-line {
    position: absolute;
    left: 0; width: 100%;
    text-align: center;
    font-weight: 700;
    font-size: 10px;
    letter-spacing: 0.3px;
    color: var(--navy);
  }
  .card--front-a .services-line { top: 260px; }
  .card--front-c .services-line { top: 259px; color: var(--paper); font-size: 9.5px; }

  .services-list {
    position: absolute;
    right: 8px; top: 173px;
    list-style: none;
    text-align: right;
    color: var(--navy);
    font-weight: 700;
    font-size: 12.5px;
    letter-spacing: 0.4px;
    line-height: 19.6px;
  }

  .initials {
    position: absolute;
    left: 40px; top: 76px;
    color: var(--navy);
    font-weight: 700;
    font-size: 112px;
    line-height: 1;
    letter-spacing: -4px;
  }
  .divider {
    position: absolute;
    left: 226px; top: 73px;
    width: 1px; height: 141px;
    background: var(--rule);
  }
  .contact { position: absolute; left: 271px; top: 70px; color: var(--ink); }
  .contact__name { color: var(--navy); font-weight: 700; font-size: 22px; line-height: 1.1; }
  .contact__address { font-size: 8.5px; line-height: 11px; margin-top: 1px; }
  .contact__phones { font-size: 10.5px; line-height: 13px; margin-top: 13px; }
  .contact__phones b { display: inline-block; width: 32px; }
  .contact__web { font-size: 10.5px; line-height: 13px; margin-top: 7px; }
</style>
</head>
<body>

  <section class="card card--front-a">
    <div class="wordmark">RM Wendt</div>
    <p class="services-line">FENSTER | TÜREN | ROLLLÄDEN | RAFFSTOREN | INSEKTENSCHUTZ</p>
  </section>

  <section class="card card--back">
    <svg class="shape" viewBox="0 0 469 287" aria-hidden="true">
      <polygon points="0,0 221,0 198,17 0,17" fill="var(--navy)"/>
      <polygon points="248,287 272,270 469,270 469,287" fill="var(--navy)"/>
    </svg>
    <div class="initials">RM</div>
    <div class="divider"></div>
    <div class="contact">
      <h1 class="contact__name">Rolf Wendt</h1>
      <p class="contact__address">Tannenweg 12<br>79000 Musterdorf-Talheim</p>
      <p class="contact__phones">
        <b>Mobil</b>: 0170 000 12 34<br>
        <b>Büro</b>: 07700 123 45 67<br>
        <b>Fax</b>: 03200 987 65 43
      </p>
      <p class="contact__web">wendt@mail-muster.de<br>www.rolf-wendt-muster.de</p>
    </div>
  </section>

  <section class="card card--front-b">
    <svg class="shape" viewBox="0 0 469 287" aria-hidden="true">
      <polygon points="329,287 346,270 469,270 469,287" fill="var(--navy)"/>
    </svg>
    <div class="wordmark">RM Wendt</div>
    <ul class="services-list">
      <li>FENSTER</li>
      <li>TÜREN</li>
      <li>ROLLLÄDEN</li>
      <li>RAFFSTOREN</li>
      <li>INSEKTENSCHUTZ</li>
    </ul>
  </section>

  <section class="card card--front-c">
    <svg class="shape" viewBox="0 0 469 287" aria-hidden="true">
      <rect x="0" y="0" width="469" height="11" fill="var(--navy)"/>
      <rect x="0" y="259" width="469" height="28" fill="var(--navy)"/>
    </svg>
    <div class="wordmark">RM Wendt</div>
    <p class="services-line" style="top:267px">FENSTER | TÜREN | ROLLLÄDEN | RAFFSTOREN | INSEKTENSCHUTZ</p>
  </section>

</body>
</html>
```